Business Card Design - Amberfield Court

We are looking at a new design for our business cards that has a modern and professional look. We run a residential aged care facility focussing on the care of residents. The cards will be used for potential clients, consultants and business opportunities in this sector. Blue and white is our main colours and would to see these colours incorporated in the design.
Industry/Entity Type
Business
Contact Information for Business Card
Amberfield Court, Darren Walsh, dwalsh@amberfieldcourt.com.au, Finance Manager, 0472 639 208, BCom, 37 Marrabel Crescent, Brindle Vale, Qld 4093.
Look and feel
Each slider illustrates characteristics of the customer's brand and the style your logo design should communicate.

```html
<!DOCTYPE html>
<html lang="en">
<head>
<meta charset="utf-8">
<title>Amberfield Court – Business Card</title>
<link rel="stylesheet" href="https://fonts.googleapis.com/css2?family=Arimo:wght@400;700&display=swap">
<style>
  :root {
    --page-bg: #e9e7e5;
    --card-white: #ffffff;
    --card-shade: #f1f1f1;
    --brand-blue: #4b7b96;
    --brand-taupe: #9b8b83;
    --back-grey: #8b837e;
    --back-grey-dark: #6f6864;
    --back-mark: #c9c5c2;
    --ink: #3a3a3a;
    --divider: #c8c8c8;
  }
  * { box-sizing: border-box; margin: 0; padding: 0; }
  html, body {
    width: 1200px; height: 950px; overflow: hidden;
    background: var(--page-bg);
    font-family: "Arimo", Arial, sans-serif;
  }
  .sheet {
    position: relative; width: 1200px; height: 950px;
    display: flex; flex-direction: column; align-items: center; justify-content: center; gap: 50px;
  }
  .card {
    position: relative; width: 700px; height: 400px; overflow: hidden;
    box-shadow: 0 6px 18px rgba(0,0,0,.18);
  }

  /* Front */
  .card--front {
    background: linear-gradient(160deg, var(--card-white) 40%, var(--card-shade) 100%);
  }
  .brand {
    position: absolute; left: 24px; top: 120px; width: 296px;
    display: flex; flex-direction: column; align-items: center;
  }
  .brand__row { display: flex; align-items: center; gap: 10px; white-space: nowrap; }
  .brand__dot { flex: none; width: 18px; height: 18px; border-radius: 50%; background: var(--brand-blue); }
  .brand__name {
    font-size: 23px; font-weight: 700; letter-spacing: 1px; text-transform: uppercase;
    color: var(--brand-blue);
  }
  .brand__tagline {
    margin-top: 10px; width: 100%; text-align: center;
    padding: 4px 0; font-size: 15px; color: var(--card-white);
    background: var(--brand-taupe); letter-spacing: .3px;
  }
  .divider {
    position: absolute; left: 338px; top: 70px; width: 1px; height: 210px;
    background: linear-gradient(to bottom, transparent, var(--divider) 20%, var(--divider) 80%, transparent);
  }
  .contact {
    position: absolute; left: 362px; top: 82px; color: var(--ink);
  }
  .contact__name { font-size: 24px; font-weight: 700; color: var(--brand-blue); }
  .contact__name small { font-size: 15px; margin-left: 4px; }
  .contact__role { font-size: 16px; color: var(--brand-taupe); margin-top: 4px; margin-bottom: 14px; }
  .contact__line { font-size: 16px; line-height: 23px; display: flex; align-items: center; gap: 8px; }
  .contact__line svg { width: 14px; height: 14px; flex: none; fill: var(--ink); }
  .contact__address { font-size: 16px; line-height: 21px; margin-bottom: 8px; }
  .foot-band { position: absolute; left: 0; bottom: 0; width: 700px; height: 22px; }

  /* Back */
  .card--back {
    background: linear-gradient(135deg, var(--back-grey) 0%, var(--back-grey-dark) 100%);
    display: flex; flex-direction: column; align-items: center; justify-content: center;
  }
  .back-mark { display: flex; align-items: center; gap: 16px; white-space: nowrap; }
  .back-mark__dot { flex: none; width: 34px; height: 34px; border-radius: 50%; background: var(--back-mark); }
  .back-mark__name {
    font-size: 40px; font-weight: 700; letter-spacing: 1.5px; text-transform: uppercase; color: var(--back-mark);
  }
  .back-web { margin-top: 22px; font-size: 20px; color: var(--back-mark); letter-spacing: .5px; }
</style>
</head>
<body>
<main class="sheet">
  <section class="card card--front" aria-label="Business card front">
    <div class="brand">
      <div class="brand__row">
        <span class="brand__dot"></span>
        <span class="brand__name">Amberfield Court</span>
      </div>
      <p class="brand__tagline">Comfort, Respect, Community</p>
    </div>
    <div class="divider"></div>
    <div class="contact">
      <p class="contact__name">Darren Walsh <small>BCom</small></p>
      <p class="contact__role">Finance Manager</p>
      <p class="contact__address">37 Marrabel Crescent<br>Brindle Vale, Qld 4093.</p>
      <p class="contact__line">
        <svg viewBox="0 0 16 16"><path d="M3 1h3l1.5 4-2 1.2a9 9 0 0 0 4.3 4.3L11 8.5l4 1.5v3c0 1-1 2-2 2C7 15 1 9 1 3c0-1 1-2 2-2z"/></svg>
        0472 639 208
      </p>
      <p class="contact__line">
        <svg viewBox="0 0 16 16"><path d="M1 3h14v10H1z M1 3l7 6 7-6" fill="none" stroke="#3a3a3a" stroke-width="1.6"/></svg>
        dwalsh@amberfieldcourt.com.au
      </p>
      <p class="contact__line">
        <svg viewBox="0 0 16 16"><circle cx="8" cy="8" r="7"/><path d="M2 8h12M8 1c3 3 3 11 0 14M8 1c-3 3-3 11 0 14" fill="none" stroke="#fff" stroke-width="1"/></svg>
        www.amberfieldcourt.com.au
      </p>
    </div>
    <svg class="foot-band" viewBox="0 0 700 22" preserveAspectRatio="none" aria-hidden="true">
      <polygon points="0,0 390,0 376,22 0,22" fill="var(--brand-blue)"/>
      <polygon points="398,0 700,0 700,22 384,22" fill="var(--brand-taupe)"/>
    </svg>
  </section>

  <section class="card card--back" aria-label="Business card back">
    <div class="back-mark">
      <span class="back-mark__dot"></span>
      <span class="back-mark__name">Amberfield Court</span>
    </div>
    <p class="back-web">www.amberfieldcourt.com.au</p>
  </section>
</main>
</body>
</html>
```